Computer consultant business card

Bexil Software is a newly started computer consulting company. It's a small one-man company that provides mostly Vornix applications but also websites in collaboration with designers. I'm running this company on the side of full time university studies.

I want the final design to be clean and memorable. Be creative! :)

Some inspiration:
http://www.pixelmarta.com/design/48317
http://www.pixelmarta.com/design/2739164/business-card-design-by-frostlynk
http://www.pixelmarta.com/design/604281/business-card-design-by-koralind-vestrabanu

See attachment for my company logo.
Updates

I would like to thank everyone for submitting! I'll need a couple of days to review and ultimately select a design.

Target Market(s)

Non-technical entrepreneurs and small companies.

Industry/Entity Type

University

Requirements
Must have
• My company logo.
In any way, both colors from my logo.
First- and last name, e-mail and phone number.
Double-sided design.
Nice to have
• Something creative with the symbol in my logo

```html
<!DOCTYPE html>
<html lang="en">
<head>
<meta charset="utf-8">
<title>Zorvi – Business Card</title>
<link rel="stylesheet" href="https://fonts.googleapis.com/css2?family=Comfortaa:wght@700&family=Open+Sans:wght@400;600;700&display=swap">
<style>
  :root {
    --backdrop: #e9e4dc;
    --ink: #333336;
    --ink-soft: #55565b;
    --brand-blue: #4a72b8;
    --paper: #ffffff;
    --night: #050505;
    --slate: #303139;
    --slate-blue: #4d5d87;
    --ghost: #ececf2;
    --rule: #8a8a8f;
  }
  * { box-sizing: border-box; margin: 0; padding: 0; }
  html, body { width: 1200px; height: 788px; overflow: hidden; }
  body {
    position: relative;
    background: var(--backdrop);
    font-family: "Open Sans", Arial, sans-serif;
    color: var(--ink);
  }
  .side-label {
    position: absolute;
    width: 525px;
    text-align: center;
    font-size: 20px;
    color: #1d1d1d;
  }
  .card {
    position: absolute;
    width: 525px;
    height: 299px;
    border-radius: 22px;
    overflow: hidden;
    box-shadow: 0 3px 10px rgba(0,0,0,.25);
  }
  .card--front { left: 54px; top: 75px; background: var(--paper); }
  .card--back-light { left: 622px; top: 75px; background: var(--paper); }
  .card--back-dark { left: 54px; top: 446px; background: var(--night); }
  .card--back-slate {
    left: 622px; top: 446px;
    background: radial-gradient(ellipse 80% 90% at 55% 100%, var(--slate-blue), var(--slate) 75%);
  }

  .brand { position: absolute; display: flex; align-items: center; }
  .brand__dot { border-radius: 50%; background: var(--brand-blue); flex: none; }
  .brand__name {
    font-family: "Comfortaa", "Open Sans", sans-serif;
    font-weight: 700; line-height: 1;
  }

  .card--front .brand { left: 37px; top: 37px; gap: 20px; }
  .card--front .brand__dot { width: 74px; height: 74px; }
  .card--front .brand__name { font-size: 62px; color: var(--ink); }

  .brand--centred { left: 0; right: 0; top: 90px; justify-content: center; gap: 26px; }
  .brand--centred .brand__dot { width: 106px; height: 106px; }
  .brand--centred .brand__name { font-size: 90px; }
  .card--back-light .brand__name { color: var(--ink); }
  .card--back-dark .brand__name,
  .card--back-slate .brand__name { color: var(--paper); }

  .ghost-mark {
    position: absolute; left: 319px; top: 108px;
    width: 177px; height: 177px; border-radius: 50%;
    background: var(--ghost);
  }

  .contact { position: absolute; left: 48px; top: 186px; width: 248px; }
  .contact__name { margin-left: 28px; font-size: 17px; font-weight: 700; color: var(--ink); line-height: 20px; }
  .contact__role { margin-left: 28px; font-size: 12.5px; color: var(--ink-soft); line-height: 18px; }
  .contact__rule-h { position: absolute; left: 0; top: 43px; width: 248px; border-top: 1px solid var(--rule); }
  .contact__rule-v { position: absolute; left: 22px; top: 0; height: 93px; border-left: 1px solid var(--rule); }
  .contact__lines { margin-top: 8px; list-style: none; }
  .contact__lines li { display: flex; align-items: center; font-size: 14.5px; color: var(--ink); height: 20px; }
  .contact__lines svg { width: 11px; height: 11px; margin: 0 17px 0 3px; fill: var(--ink); flex: none; }

  .web {
    position: absolute; left: 0; right: 0; top: 247px;
    text-align: center; font-size: 18px; letter-spacing: 3.6px; line-height: 24px;
  }
  .card--back-dark .web, .card--back-slate .web { top: 254px; }
  .card--back-light .web { color: var(--ink); }
  .card--back-dark .web, .card--back-slate .web { color: var(--paper); }

  .texture { position: absolute; }
  .texture--upper {
    left: 0; top: 0; width: 300px; height: 120px;
    background: radial-gradient(ellipse at 45% 10%, rgba(120,120,125,.45), rgba(0,0,0,0) 70%);
  }
  .texture--lower {
    right: 0; bottom: 0; width: 230px; height: 150px;
    background: radial-gradient(ellipse at 50% 70%, rgba(140,130,135,.5), rgba(0,0,0,0) 70%);
  }
</style>
</head>
<body>
  <div class="side-label" style="left:54px;top:34px;">Front</div>
  <div class="side-label" style="left:622px;top:34px;">Back - 1</div>
  <div class="side-label" style="left:54px;top:405px;">Back - 2</div>
  <div class="side-label" style="left:622px;top:405px;">Back - 3</div>

  <section class="card card--front">
    <div class="ghost-mark"></div>
    <div class="brand">
      <span class="brand__dot"></span>
      <span class="brand__name">zorvi</span>
    </div>
    <div class="contact">
      <span class="contact__rule-v"></span>
      <span class="contact__rule-h"></span>
      <p class="contact__name">First Name + Last Name</p>
      <p class="contact__role">Designation</p>
      <ul class="contact__lines">
        <li><svg viewBox="0 0 12 12"><path d="M2.5 1l2 2.2-1 1.3c.6 1.4 1.6 2.4 3 3l1.3-1 2.2 2-1.2 1.7C5.3 10 2 6.7 1 2.2z"/></svg>+12 345 6789</li>
        <li><svg viewBox="0 0 12 12"><path d="M1 3h10v6H1z M1 3l5 3.5L11 3" fill="none" stroke="#333336" stroke-width="1.2"/></svg>info@zorvi.com</li>
      </ul>
    </div>
  </section>

  <section class="card card--back-light">
    <div class="brand brand--centred">
      <span class="brand__dot"></span>
      <span class="brand__name">zorvi</span>
    </div>
    <p class="web">www.zorvi.com</p>
  </section>

  <section class="card card--back-dark">
    <div class="texture texture--upper" role="img" aria-label="Perforated metal dot texture, upper corner"></div>
    <div class="texture texture--lower" role="img" aria-label="Perforated metal dot texture, lower corner"></div>
    <div class="brand brand--centred">
      <span class="brand__dot"></span>
      <span class="brand__name">zorvi</span>
    </div>
    <p class="web">www.zorvi.com</p>
  </section>

  <section class="card card--back-slate">
    <div class="brand brand--centred">
      <span class="brand__dot"></span>
      <span class="brand__name">zorvi</span>
    </div>
    <p class="web">www.zorvi.com</p>
  </section>
</body>
</html>
```